Designing a brochures for an educational counseling service provider

We would like a 4 sided design on a 11x8.5 paper, half folded. I have including a sample design we did to give you an idea of what we envision but we welcome creativity to make beautiful looking flyers. Text for the flier is included as well as our logo.
- The most important thing is capturing our audience/market. We will be handing these flies to schools, organizations and individual clients.

www.pvrlearningadvisors.example

Target Market(s)

We are targeting international students wanting to study in the U.S and Canada.

Industry/Entity Type

Education

Requirements
Must have
• - Clean and clear
• - Our logo should visible and well placed.
• - Could you the pictures of students, libraries and school buildings or you could use the pictures we already have.
Nice to have
• We would like this to match business cards.

```html
<!DOCTYPE html>
<html lang="en">
<head>
<meta charset="utf-8">
<title>PVR Learning Advisors – Brochure Spread</title>
<link rel="stylesheet" href="https://fonts.googleapis.com/css2?family=Raleway:wght@400;500;600;700&family=Open+Sans:wght@400;600;700&display=swap">
<style>
  :root{
    --navy:#262f7d;
    --blue:#1f6cc0;
    --green:#5db52f;
    --green-light:#8dc63f;
    --ink:#2a2a2a;
    --paper:#ffffff;
    --mist:#e9ecef;
    --bg:#dcdcdc;
  }
  *{box-sizing:border-box;margin:0;padding:0}
  html,body{width:1200px;height:900px;overflow:hidden;background:var(--bg)}
  .spread{position:absolute;left:70px;top:40px;width:1060px;height:820px;display:flex;box-shadow:0 6px 24px rgba(0,0,0,.18)}
  .panel{position:relative;width:530px;height:820px;background:var(--paper);overflow:hidden}

  /* back cover */
  .copy{position:absolute;left:32px;top:28px;right:30px;font-family:"Raleway",sans-serif;color:var(--ink);font-size:13px;line-height:1.42}
  .section-tag{display:inline-block;background:linear-gradient(90deg,var(--green),var(--green-light));color:#fff;font-family:"Open Sans",sans-serif;font-weight:700;font-size:13px;padding:2px 40px 2px 8px;margin:6px 0 4px}
  .copy p{margin-bottom:8px}
  .back-photo{position:absolute;left:0;top:372px;width:530px;height:248px;background:linear-gradient(120deg,#d9b79c 0%,#c65a7a 35%,#3b7fc4 60%,#e0577a 80%,#7bb84a 100%)}
  .back-footer{position:absolute;left:0;top:620px;width:530px;height:140px;display:flex;align-items:center;padding:0 28px}
  .brand{display:flex;align-items:center;gap:10px;font-family:"Raleway",sans-serif;font-weight:700;color:var(--navy)}
  .brand-dot{width:34px;height:34px;border-radius:50%;background:var(--green)}
  .brand-name{font-size:20px;line-height:1.1}
  .back-footer .brand{width:200px;flex-shrink:0}
  .contact{border-left:2px solid var(--green);padding-left:12px;font-family:"Open Sans",sans-serif;font-size:11px;line-height:1.4;color:var(--ink)}
  .contact h3{color:var(--green);font-size:12px;font-weight:700}
  .contact strong{display:block;font-weight:700}
  .back-bar{position:absolute;left:0;bottom:0;width:530px;height:60px;background:var(--navy)}

  /* front cover */
  .front{background:linear-gradient(180deg,#f4f5f6,var(--mist))}
  .front .brand{position:absolute;right:34px;top:52px}
  .front-art{position:absolute;left:0;top:0}
  .tagline{position:absolute;left:0;top:520px;width:530px;height:82px;background:linear-gradient(90deg,var(--navy),var(--blue));color:#fff;font-family:"Raleway",sans-serif;font-weight:700;font-size:18px;line-height:1.3;text-align:center;display:flex;align-items:center;justify-content:center;padding:0 24px}
  .services{position:absolute;left:0;top:602px;width:530px;height:158px;background:linear-gradient(90deg,var(--green-light),var(--green));display:flex;justify-content:space-around;align-items:center;padding:0 12px}
  .service{display:flex;flex-direction:column;align-items:center;gap:10px;color:#fff;font-family:"Open Sans",sans-serif;font-size:11px;font-weight:600;width:110px;text-align:center}
  .service-icon{width:54px;height:54px;border:2px solid #fff;border-radius:4px;display:flex;align-items:center;justify-content:center}
  .front-bar{position:absolute;left:0;bottom:0;width:530px;height:60px;background:var(--navy)}
  .front-bar::before{content:"";position:absolute;left:0;top:10px;width:100%;height:8px;background:var(--blue)}
</style>
</head>
<body>
<main class="spread">
  <section class="panel back">
    <div class="copy">
      <span class="section-tag">Transfer students</span>
      <p>Need to find a school an alternative school that is a better match for you? We work with students and families to transfer from one school to another.</p>
      <span class="section-tag">Boarding schools</span>
      <p>Funding the education for your children in some of the world's top schools can be very expensive as tuition and fees increase at an average of 4% every year. We work with you to determine the budget for your family, applying to scholarship available and guide you through the financial aid process.</p>
      <p>Over 70% of our clients have been awarded scholarships or Financial Aid, making your education goals attainable an affordable and your children education possible.</p>
      <p>Include at the bottom of last page "Our consultants are members of the Harborview Study Guild, a regional circle of student placement advisors."</p>
    </div>
    <div class="back-photo" role="img" aria-label="Photo of a smiling group of students giving thumbs up"></div>
    <div class="back-footer">
      <div class="brand"><span class="brand-dot"></span><span class="brand-name">PVR Learning Advisors</span></div>
      <div class="contact">
        <h3>CONTACT US</h3>
        <strong>Executive Director &amp; Independent Educational Consultant</strong>
        PVR Learning Advisors, LLC,<br>
        418 Alder Court, Suite 12, Maple Ridge, TX 75000<br>
        Phone: 555-014-2298<br>
        Email: hello@pvrlearningadvisors.example
      </div>
    </div>
    <div class="back-bar"></div>
  </section>

  <section class="panel front">
    <svg class="front-art" width="530" height="520" viewBox="0 0 530 520">
      <defs>
        <linearGradient id="photoTone" x1="0" y1="0" x2="1" y2="1">
          <stop offset="0" stop-color="#6f9a4c"/>
          <stop offset=".45" stop-color="#3d6fa8"/>
          <stop offset=".75" stop-color="#c9a68f"/>
          <stop offset="1" stop-color="#8fb0c8"/>
        </linearGradient>
      </defs>
      <path role="img" aria-label="Photo of five smiling students holding notebooks outdoors" d="M0,150 L270,150 Q420,190 510,520 L0,520 Z" fill="url(#photoTone)"/>
      <path d="M276,152 Q424,194 512,520" fill="none" stroke="var(--blue)" stroke-width="10"/>
      <path d="M262,140 Q430,178 524,520" fill="none" stroke="var(--navy)" stroke-width="3"/>
    </svg>
    <div class="brand"><span class="brand-dot"></span><span class="brand-name">PVR Learning Advisors</span></div>
    <div class="tagline">A full - service international educational consulting group serving students and families across the globe</div>
    <div class="services">
      <div class="service">
        <span class="service-icon"><svg width="30" height="30" viewBox="0 0 30 30" fill="none" stroke="#fff" stroke-width="2"><path d="M3 11 L15 4 L27 11 Z"/><path d="M7 13v10M12 13v10M18 13v10M23 13v10M3 26h24"/></svg></span>
        Boarding Schools
      </div>
      <div class="service">
        <span class="service-icon"><svg width="30" height="30" viewBox="0 0 30 30" fill="none" stroke="#fff" stroke-width="2"><path d="M6 3h13l5 5v19H6Z"/><path d="M10 12h9M10 17h6M14 24l10-10 2 2-10 10h-2Z"/></svg></span>
        College Admission
      </div>
      <div class="service">
        <span class="service-icon"><svg width="30" height="30" viewBox="0 0 30 30" fill="none" stroke="#fff" stroke-width="2"><rect x="3" y="4" width="24" height="22" rx="2"/><circle cx="11" cy="12" r="3"/><circle cx="19" cy="12" r="3"/><path d="M6 22c1-4 9-4 10 0M14 22c1-4 9-4 10 0"/></svg></span>
        Transfer Students
      </div>
      <div class="service">
        <span class="service-icon"><svg width="30" height="30" viewBox="0 0 30 30" fill="none" stroke="#fff" stroke-width="2"><path d="M2 11 L15 5 L28 11 L15 17 Z"/><path d="M8 14v6c3 3 11 3 14 0v-6M26 12v8"/></svg></span>
        Graduate Students
      </div>
    </div>
    <div class="front-bar"></div>
  </section>
</main>
</body>
</html>
```